I need a label with logo to go on jars of honey.
Label size 70mm x 70mm
The front label should say :
The Fenwick Honey Co. (logo)
Tarapeka Honey
400g
The back label:
Would have nutritional information
And our address
You can see from the uploaded files the styles I prefer, I have uploaded a photo of the honey product too. The background of the logo doesn't have to be white. I would like to develop a color scheme that would look nice against the color of the honey.
Logo Text
The Fenwick Honey Co. / The Fenwick Honey Company

```html
<!DOCTYPE html>
<html lang="en">
<head>
<meta charset="utf-8">
<title>The Fenwick Honey Co. – Tarapeka Honey Front Label</title>
<link rel="stylesheet" href="https://fonts.googleapis.com/css2?family=Cutive&display=swap">
<style>
  :root {
    --page-bg: #ffffff;
    --label-cream: #e5e0c4;
    --label-frame: #9c8677;
    --ink-brown: #8f7464;
  }

  * { box-sizing: border-box; margin: 0; padding: 0; }

  html, body {
    width: 1015px;
    height: 1200px;
    overflow: hidden;
    background: var(--page-bg);
  }

  .canvas {
    width: 1015px;
    height: 1200px;
    display: flex;
    align-items: center;
    justify-content: center;
  }

  .front-label {
    width: 640px;
    height: 640px;
    background: var(--label-cream);
    border: 9px solid var(--label-frame);
    display: flex;
    flex-direction: column;
    align-items: center;
    font-family: "Cutive", "Courier New", serif;
    color: var(--ink-brown);
    text-align: center;
  }

  .brand {
    margin-top: 78px;
    display: flex;
    flex-direction: column;
    align-items: center;
  }

  .brand-mark {
    width: 150px;
    height: 150px;
    display: block;
  }

  .brand-name {
    margin-top: 30px;
    font-size: 40px;
    font-weight: 400;
    letter-spacing: 1px;
    white-space: nowrap;
  }

  .product-name {
    margin-top: 86px;
    font-size: 48px;
    font-weight: 400;
  }

  .net-weight {
    margin-top: 30px;
    font-size: 38px;
    font-weight: 400;
  }
</style>
</head>
<body>
  <main class="canvas">
    <section class="front-label" aria-label="Front jar label">
      <header class="brand">
        <svg class="brand-mark" viewBox="0 0 150 150" aria-hidden="true">
          <circle cx="75" cy="75" r="70" fill="none" stroke="var(--ink-brown)" stroke-width="5"/>
        </svg>
        <h1 class="brand-name">The Fenwick Honey Co.</h1>
      </header>
      <p class="product-name">Tarapeka Honey</p>
      <p class="net-weight">400g</p>
    </section>
  </main>
</body>
</html>
```